A website where experts collaborate on your project

I am building a new website where experts (yes, like designers) collaborate on projects with the project owner. More minds = more collaboration = better end product. Please see Pelmora(dot)com for a quick landing page I created for collaborating on presentations (although there will be many project types offered)

I am looking for a DESIGNER LONG TERM, but for now, just need initial mock ups to show the web programmers.

I have 21 Word documents loosely designed, what I would like to see here is a theme. Please DO NOT GO OFF WHAT YOU CURRENTLY SEE AT PELMORA. What is up now is only a quick landing page.

You can view a Word doc of the homepage here:
https://www.filevanta.com/s/qx83kdm2/home.docx?dl=0

WHAT AM I LOOKING FOR?
A clean, well designed theme.

Here is a link to the logo:
https://www.filevanta.com/s/mr47tpz9/logo%20-%20horizontal.tif?dl=0
-----------------------------------------
Here are a few sites I like the design of and what I like about them:
www.quenbrook.com-all around my favorite, beautiful graphics, clean layout, bold use of colors on a dark background
Ravelto.com- clean layout, The use of humans and bubble style elements.
Mintharbor.com :) clean, bold, unique pop art style but professional
plumevault.com - From the unique colors and artwork and the ability of that art to not interfere with the important elements of the site
sparkwidgets.com-clean, nice colors, well organized and separated sections.
www.dunmereco.com-love the font, use of colors and sectionalized style

All in all, I am not picky and open to so many styles. I would ultimately like the designer I pick to design all 21 pages.
Updates

Hello everyone,Moving forward, I would like you all to pay special attention to the section in my brief titled "Here are a few sites I like the design of and what I like about them". Please see below, I handpicked each one of these as sites I really like. Thank you.Here are a few sites I like the design of and what I like about them:Ravelto.com- clean layout, The use of humans and bubble style elements.Mintharbor.com :) clean, bold, unique pop art style but professionalwriteraccess.com - From the unique colors and artwork and the ability of that art to not interfere with the important elements of the sitegrowthgeeks.com-clean, nice colors, well organized and separated sections.www.dunmereco.com-love the font, use of colors and sectionalized stylewww.quenbrook.com-beautiful graphics, clean layout, bold use of colors----------------------------------------- Added Tuesday, November 24, 2015

I updated the homepage, you can see it here:https://www.dropbox.com/s/kwlkbsookq3cg2m/1new%20homepage.docx?dl=0I am modeling it after my favorite designed site: triplelift.comI love the dark colors with the orange glowing style boldness of the buttons. It's real clean too. Added Tuesday, November 24, 2015

Target Market(s)

small business owners, marketers, freelancer writers, graphic designers,

Industry/Entity Type

Building

Number of Pages Required

5+ page

Requirements
Must have
• I can't think of anything the project must have.
Nice to have
• WHAT AM I LOOKING FOR?
• A clean, well designed theme. I had a designer do a bit of work putting elements together, I found it to be very plain, but I like the Application Page (https://www.filevanta.com/s/jb19ckr3/Pelmora-Website.ai?dl=0)
• Here is a link to the logo:
• https://www.filevanta.com/s/mr47tpz9/logo%20-%20horizontal.tif?dl=0
• Here are a few sites I like the design of and what I like about them:
• Ravelto.com- clean layout, The use of humans and bubble style elements.
• Mintharbor.com :) clean, bold, unique pop art style but professional
• plumevault.com - From the unique colors and artwork and the ability of that art to not interfere with the important elements of the site
• sparkwidgets.com-clean, nice colors, well organized and separated sections.
• www.dunmereco.com-love the font, use of colors and sectionalized style
• www.quenbrook.com-beautiful graphics, clean layout, bold use of colors
• -----------------------------------------
Should not have
• out of the boxed, templated style website. I want this site to be memorable and not look like a thousand others

```html
<!DOCTYPE html>
<html lang="en">
<head>
<meta charset="utf-8">
<title>Pelmora — Crowd Projects</title>
<link rel="stylesheet" href="https://fonts.googleapis.com/css2?family=Roboto:wght@400;500;700&family=Roboto+Condensed:wght@400;700&family=Open+Sans:ital,wght@0,400;0,600;1,400&display=swap">
<style>
  :root{
    --teal:#4aa8c6;
    --teal-dark:#3a95b3;
    --orange:#f08a1c;
    --orange-dark:#e07a10;
    --ink:#333;
    --muted:#666;
    --line:#e3e3e3;
    --panel:#f5f5f5;
    --footer:#0d0f12;
    --link-blue:#5aaed0;
  }
  *{box-sizing:border-box;margin:0;padding:0}
  html,body{width:712px;height:1200px;overflow:hidden;background:#fff}
  body{position:relative;font-family:"Open Sans",Arial,sans-serif;color:var(--ink)}
  .abs{position:absolute}

  /* header */
  .top-rule{left:0;top:0;width:712px;height:2px;background:var(--teal)}
  .brand{left:59px;top:24px;display:flex;align-items:center;gap:8px}
  .brand-name{font-family:"Roboto",sans-serif;font-weight:500;font-size:17px;color:var(--orange)}
  .brand-dot{width:28px;height:28px;border-radius:50%;background:var(--orange)}
  .promo{left:413px;top:17px;width:240px;height:35px;background:var(--orange);border-radius:8px;color:#fff;font-size:6.4px;line-height:10px;padding:7px 12px}
  .promo-tail{left:630px;top:50px}

  /* nav */
  .navbar{left:0;top:71px;width:712px;height:33px;background:var(--teal)}
  .search{left:58px;top:76px;width:135px;height:22px;background:#fff;border-radius:11px;font-size:6.5px;color:#555;padding:6px 9px}
  .search svg{position:absolute;right:10px;top:7px}
  .nav-item{top:71px;height:33px;line-height:33px;font-family:"Roboto Condensed",sans-serif;font-size:7.5px;color:#fff;text-align:center;letter-spacing:.2px}
  .nav-item.active{background:var(--orange)}
  .nav-sep{top:79px;width:1px;height:17px;background:rgba(255,255,255,.25)}

  /* hero */
  .hero{left:0;top:104px;width:712px;height:310px;background:linear-gradient(100deg,#c9c2b4 0%,#a99b86 35%,#4d5566 62%,#c8bba6 85%,#e6ddd0 100%)}
  .hero-title{left:68px;top:222px;font-family:"Roboto Condensed",sans-serif;font-weight:700;font-size:24px;color:#fff;letter-spacing:.2px}
  .hero-sub{left:70px;top:254px;font-family:"Roboto",sans-serif;font-size:9px;color:#fff}
  .hero-btn{left:70px;top:277px;width:82px;height:27px;background:var(--orange);border:1px solid #f7b46c;border-radius:2px;color:#fff;font-family:"Roboto",sans-serif;font-size:9px;text-align:center;line-height:25px}
  .hero-arrow{top:245px;width:20px;height:20px;border-radius:50%;background:rgba(60,60,60,.55)}
  .hero-arrow svg{position:absolute;left:6px;top:5px}

  /* sidebar */
  .panel{left:58px;width:144px;border:1px solid var(--line);background:#fff}
  .panel-head{height:24px;background:var(--panel);font-family:"Roboto",sans-serif;font-size:9.5px;color:#444;padding:6px 9px;position:relative}
  .panel-head::after{content:"";position:absolute;right:10px;top:11px;width:9px;height:1.5px;background:#999}
  .price-label{font-size:7.5px;color:#444;margin:10px 9px 0;padding-bottom:6px;border-bottom:1px solid var(--line);display:flex;align-items:center;gap:6px}
  .price-row{display:flex;align-items:center;gap:5px;font-size:7.5px;color:#555;margin:12px 9px 0}
  .price-row span.box{border:1px solid var(--line);width:41px;height:16px;font-size:6.5px;text-align:center;line-height:14px}
  .slider{margin:10px 9px 0;height:8px;border:1px solid #ddd;border-radius:4px;background:#f3f3f3;position:relative}
  .slider i{position:absolute;left:22px;width:59px;top:2px;height:3px;background:var(--orange-dark)}
  .slider b{position:absolute;top:-1px;width:7px;height:8px;border-radius:50%;background:#fff;border:1px solid #bbb}
  .country-list{list-style:none}
  .country-list li{height:17.8px;border-bottom:1px solid #efefef;font-size:7px;color:#444;padding:4px 9px;position:relative}
  .country-list li.more::after{content:"+";position:absolute;right:9px;top:3px;font-size:9px;color:#777}
  .acc{left:58px;width:144px;height:24px;background:var(--panel);font-family:"Open Sans",sans-serif;font-size:9px;color:#555;padding:5px 10px}
  .acc::after{content:"+";position:absolute;right:9px;top:0;font-size:15px;color:#aaa;font-weight:300}
  .save{left:58px;top:945px;width:144px;height:24px;background:var(--orange);color:#fff;font-size:8.5px;padding:6px 10px}
  .save::after{content:"+";position:absolute;right:9px;top:0;font-size:15px}

  /* projects */
  .proj-head{left:226px;top:434px;width:428px;height:31px;border:1px solid #ddd;box-shadow:0 1px 2px rgba(0,0,0,.12);background:#fff}
  .proj-head h2{position:absolute;left:11px;top:7px;font-family:"Roboto",sans-serif;font-weight:400;font-size:12px;color:#444;width:130px}
  .proj-head .shade{position:absolute;left:0;top:0;width:140px;height:29px;background:linear-gradient(90deg,#fff,#f2f2f2)}
  .sort{position:absolute;left:212px;top:9px;font-size:9px;color:#555}
  .select{position:absolute;top:7px;height:16px;border:1px solid #ddd;font-size:6.5px;color:#555;padding:3px 6px}
  .select::after{content:"";position:absolute;right:6px;top:6px;border:3px solid transparent;border-top:3.5px solid #555}
  .card-img{left:226px;width:111px;height:92px;border:1px solid #cde3ec}
  .card-mark{left:353px;width:22px;height:22px;border-radius:50%;background:var(--orange)}
  .card-title{left:399px;font-family:"Open Sans",sans-serif;font-size:9px;color:#444}
  .card-meta{left:399px;font-size:8.5px;color:var(--link-blue)}
  .card-body{left:353px;width:302px;font-size:6.3px;line-height:11px;color:#555;text-align:justify}
  .card-more{left:353px;font-size:6.5px;color:#333;text-decoration:underline;font-weight:600}

  /* testimonials */
  .testi{left:0;top:990px;width:712px;height:142px;background:linear-gradient(180deg,#f4f4f4,#fafafa 50%,#f2f2f2)}
  .testi-title{left:0;width:712px;top:1016px;text-align:center;font-family:"Roboto",sans-serif;font-size:14px;color:var(--orange-dark);letter-spacing:.5px}
  .testi-arrow{top:1019px}
  .quote{left:180px;width:352px;top:1046px;text-align:center;font-style:italic;font-size:8.5px;line-height:15px;color:#555}
  .author{left:0;width:712px;top:1091px;text-align:center;font-size:9px;color:#333}
  .author b{color:var(--orange-dark);font-weight:600}

  /* footer */
  .footer{left:0;top:1132px;width:712px;height:68px;background:var(--footer)}
  .social{top:1144px;width:18px;height:18px;border-radius:50%;background:#fff}
  .copy{left:0;width:712px;top:1174px;text-align:center;font-size:6.5px;color:#ddd}
</style>
</head>
<body>
  <div class="abs top-rule"></div>
  <div class="abs brand"><span class="brand-name">Pelmora</span><span class="brand-dot"></span></div>
  <div class="abs promo">Lorem ipsum dolor sit amet, consectetur adipiscing elit, sed do eiusmod tempor incididunt ut labore et dolore magna aliqua. Ut enim</div>
  <svg class="abs promo-tail" width="12" height="9" viewBox="0 0 12 9"><path d="M0 0H12L3 9Z" fill="#f08a1c"/></svg>

  <nav class="abs navbar"></nav>
  <div class="abs search">Browse
    <svg width="8" height="8" viewBox="0 0 10 10"><circle cx="4" cy="4" r="3" fill="none" stroke="#444" stroke-width="1.5"/><path d="M6.3 6.3L9 9" stroke="#444" stroke-width="1.5"/></svg>
  </div>
  <div class="abs nav-item active" style="left:227px;width:48px">HOME</div>
  <div class="abs nav-item" style="left:280px;width:64px">PROJECTS</div>
  <div class="abs nav-sep" style="left:348px"></div>
  <div class="abs nav-item" style="left:350px;width:80px">HOW IT WORKS</div>
  <div class="abs nav-sep" style="left:436px"></div>
  <div class="abs nav-item" style="left:438px;width:68px">PLANS</div>
  <div class="abs nav-sep" style="left:506px"></div>
  <div class="abs nav-item" style="left:507px;width:72px">MY ACCOUNT</div>
  <div class="abs nav-sep" style="left:580px"></div>
  <div class="abs nav-item" style="left:582px;width:84px">CONTACT US</div>

  <section class="abs hero" role="img" aria-label="Photo of a bearded man in glasses and a suit writing notes at a desk in a bright office"></section>
  <h1 class="abs hero-title">CONVERT MORE CUSTOMERS</h1>
  <p class="abs hero-sub">Experience the power of experts collaborating on your project.</p>
  <div class="abs hero-btn">GET STARTED</div>
  <div class="abs hero-arrow" style="left:26px"><svg width="8" height="10" viewBox="0 0 8 10"><path d="M6 1L2 5L6 9" fill="none" stroke="#fff" stroke-width="1.6"/></svg></div>
  <div class="abs hero-arrow" style="left:667px"><svg width="8" height="10" viewBox="0 0 8 10"><path d="M2 1L6 5L2 9" fill="none" stroke="#fff" stroke-width="1.6"/></svg></div>

  <!-- sidebar -->
  <div class="abs panel" style="top:434px;height:116px">
    <div class="panel-head">Filters</div>
    <div class="price-label">PRICE <svg width="6" height="4" viewBox="0 0 6 4"><path d="M0 0H6L3 4Z" fill="#555"/></svg></div>
    <div class="price-row">$ <span class="box">20.00</span> – $ <span class="box">1,000</span></div>
    <div class="slider"><i></i><b style="left:18px"></b><b style="left:78px"></b></div>
  </div>
  <div class="abs panel" style="top:568px;height:209px">
    <div class="panel-head">Country</div>
    <ul class="country-list">
      <li>Afghanistan</li><li>Albania</li><li>Cambodia</li><li>Cameroon</li><li>Canada</li>
      <li>Denmark</li><li>Djibouti</li><li>Fiji</li><li>Finland</li><li class="more">France</li>
    </ul>
  </div>
  <div class="abs acc" style="top:787px">Categories</div>
  <div class="abs acc" style="top:813px">Time Left</div>
  <div class="abs acc" style="top:838px">Active | Expired</div>
  <div class="abs acc" style="top:864px">Contains adult content</div>
  <div class="abs acc" style="top:889px">keywords</div>
  <div class="abs acc" style="top:915px">followers</div>
  <div class="abs save">Save filter</div>

  <!-- projects -->
  <div class="abs proj-head">
    <div class="shade"></div>
    <h2>Crowd Projects</h2>
    <span class="sort">Sort</span>
    <span class="select" style="left:241px;width:59px">Price</span>
    <span class="select" style="left:302px;width:60px">country</span>
    <span class="select" style="left:365px;width:58px">Time left</span>
  </div>

  <div class="abs card-img" style="top:485px;background:linear-gradient(135deg,#eef3f6,#c9d6de)" role="img" aria-label="Hands holding a tablet showing charts"></div>
  <div class="abs card-mark" style="top:486px"></div>
  <div class="abs card-title" style="top:489px">Nulla at diam ornare, aliquam urna</div>
  <div class="abs card-meta" style="top:506px">$90, CA. ,&nbsp;&nbsp; time left : 6 days</div>
  <p class="abs card-body" style="top:526px">Lorem ipsum dolor sit amet, consectetur adipiscing elit, sed do eiusmod tempor incididunt ut labore et dolore magna aliqua. Ut enim ad minim veniam, quis nostrud exercitation ullamco laboris nisi ut aliquip ex ea commodo consequat. Duis aute irure dolor</p>
  <div class="abs card-more" style="top:568px">READ MORE +</div>

  <div class="abs card-img" style="top:597px;background:linear-gradient(135deg,#e9e4dc,#b9c3cc)" role="img" aria-label="Hand with a pencil marking a printed spreadsheet"></div>
  <div class="abs card-mark" style="top:598px"></div>
  <div class="abs card-title" style="top:601px">Nulla at diam ornare, aliquam urna</div>
  <div class="abs card-meta" style="top:618px">$90, CA. ,&nbsp;&nbsp; time left : 6 days</div>
  <p class="abs card-body" style="top:638px">Lorem ipsum dolor sit amet, consectetur adipiscing elit, sed do eiusmod tempor incididunt ut labore et dolore magna aliqua. Ut enim ad minim veniam, quis nostrud exercitation ullamco laboris nisi ut aliquip ex ea commodo consequat. Duis aute irure dolor</p>
  <div class="abs card-more" style="top:680px">READ MORE +</div>

  <div class="abs card-img" style="top:714px;background:linear-gradient(135deg,#f1f1ef,#c3cbd2)" role="img" aria-label="Laptop on a white sofa showing a web page"></div>
  <div class="abs card-mark" style="top:715px"></div>
  <div class="abs card-title" style="top:718px">Nulla at diam ornare, aliquam urna</div>
  <div class="abs card-meta" style="top:735px">$90, CA. ,&nbsp;&nbsp; time left : 6 days</div>
  <p class="abs card-body" style="top:755px">Lorem ipsum dolor sit amet, consectetur adipiscing elit, sed do eiusmod tempor incididunt ut labore et dolore magna aliqua. Ut enim ad minim veniam, quis nostrud exercitation ullamco laboris nisi ut aliquip ex ea commodo consequat. Duis aute irure dolor</p>
  <div class="abs card-more" style="top:797px">READ MORE +</div>

  <div class="abs card-img" style="top:831px;background:linear-gradient(135deg,#d9dee3,#3e4c63)" role="img" aria-label="Two businessmen reviewing documents at a table"></div>
  <div class="abs card-mark" style="top:832px"></div>
  <div class="abs card-title" style="top:835px">Nulla at diam ornare, aliquam urna</div>
  <div class="abs card-meta" style="top:852px">$90, CA. ,&nbsp;&nbsp; time left : 6 days</div>
  <p class="abs card-body" style="top:872px">Lorem ipsum dolor sit amet, consectetur adipiscing elit, sed do eiusmod tempor incididunt ut labore et dolore magna aliqua. Ut enim ad minim veniam, quis nostrud exercitation ullamco laboris nisi ut aliquip ex ea commodo consequat. Duis aute irure dolor</p>
  <div class="abs card-more" style="top:914px">READ MORE +</div>

  <!-- testimonials -->
  <section class="abs testi"></section>
  <svg class="abs testi-arrow" style="left:276px" width="8" height="12" viewBox="0 0 8 12"><path d="M6 1L2 6L6 11" fill="none" stroke="#444" stroke-width="1.5"/></svg>
  <h2 class="abs testi-title" style="font-weight:400">TESTIMONIALS</h2>
  <svg class="abs testi-arrow" style="left:428px" width="8" height="12" viewBox="0 0 8 12"><path d="M2 1L6 6L2 11" fill="none" stroke="#444" stroke-width="1.5"/></svg>
  <p class="abs quote">“ With Pelmora I have multiple experts perfecting my content and I only pay for the feedback I find valuable. It’s perfect ”</p>
  <p class="abs author"><b>Dana Whitlow</b>, CEO, Ridge 14</p>

  <!-- footer -->
  <footer class="abs footer"></footer>
  <span class="abs social" style="left:310px"></span>
  <span class="abs social" style="left:338px"></span>
  <span class="abs social" style="left:367px"></span>
  <span class="abs social" style="left:396px"></span>
  <p class="abs copy">© Copyright 2015 pelmora.com. All Rights Reserved.</p>
</body>
</html>
```